Tolvik Commercial Cleaning is lookong for a new business card design.

A fresh new design that's professional and stylish. We need a serious upgrade to our business cards. I have included pictures of our existing ones. Our clients include professional individuals and business owners. We woupdblike something professional and upbeat. Please have fun and see what you come uo with.

Target Market(s)

Property managers, business owners, facility managers and other similar professionals

Industry/Entity Type

Janitorial

Contact Information for Business Card

Name, cell, office number, email, web address

Font styles to use
Sans Serif

Colors

Designer to choose colors to be used in the design.

Requirements
Must have
• please use the green color in our logo
Nice to have
• Bar code
Should not have
• Address

```html
<!DOCTYPE html>
<html lang="en">
<head>
<meta charset="utf-8">
<title>Tolvik Commercial Cleaning – Business Card</title>
<link rel="stylesheet" href="https://fonts.googleapis.com/css2?family=Montserrat:wght@400;600;700&display=swap">
<style>
  :root {
    --backdrop: #8a6e4f;
    --card-white: #ffffff;
    --brand-green: #41ad5a;
    --brand-green-deep: #2f9648;
    --ink: #333333;
  }
  * { margin: 0; padding: 0; box-sizing: border-box; }
  html, body { width: 900px; height: 1200px; overflow: hidden; }
  body {
    background: var(--backdrop);
    font-family: "Montserrat", Arial, sans-serif;
    position: relative;
  }
  .card {
    position: absolute;
    left: 80px;
    width: 742px;
    height: 440px;
    border-radius: 38px;
  }
  .card--front { top: 132px; background: var(--card-white); }
  .card--back {
    top: 638px;
    background: var(--brand-green);
    display: flex;
    align-items: center;
    justify-content: center;
  }
  .wordmark {
    position: absolute;
    left: 42px;
    top: 52px;
    width: 360px;
    font-weight: 700;
    font-size: 40px;
    line-height: 1.12;
    color: var(--brand-green);
  }
  .wordmark--back {
    position: static;
    width: auto;
    text-align: center;
    font-size: 58px;
    color: var(--brand-green-deep);
  }
  .holder {
    position: absolute;
    left: 42px;
    top: 272px;
  }
  .holder__name {
    font-weight: 600;
    font-size: 27px;
    color: var(--brand-green);
    line-height: 1.1;
  }
  .holder__role {
    font-size: 16px;
    color: var(--ink);
    margin-top: 3px;
  }
  .divider {
    position: absolute;
    left: 42px;
    top: 330px;
    width: 652px;
    height: 2px;
    background: var(--brand-green);
  }
  .contacts {
    position: absolute;
    left: 42px;
    top: 342px;
    list-style: none;
  }
  .contacts__item {
    display: flex;
    align-items: center;
    gap: 10px;
    font-size: 16px;
    color: var(--ink);
    height: 22.5px;
  }
  .contacts__icon { width: 14px; height: 14px; fill: var(--brand-green); }
</style>
</head>
<body>
  <section class="card card--front">
    <div class="wordmark">Tolvik Commercial Cleaning</div>
    <div class="holder">
      <div class="holder__name">Maren Okafor</div>
      <div class="holder__role">CEO &amp; Founder</div>
    </div>
    <div class="divider"></div>
    <ul class="contacts">
      <li class="contacts__item">
        <svg class="contacts__icon" viewBox="0 0 14 14" aria-hidden="true"><path d="M1 5c0-2 2.5-3 6-3s6 1 6 3v1h-3V4.8H4V6H1z M3 7h8l1.5 5h-11z"/></svg>
        (37) 555-0182
      </li>
      <li class="contacts__item">
        <svg class="contacts__icon" viewBox="0 0 14 14" aria-hidden="true"><path d="M1 3h12v1L7 8 1 4z M1 5.5l6 4 6-4V11H1z"/></svg>
        maren@tolvikcleaning.com
      </li>
      <li class="contacts__item">
        <svg class="contacts__icon" viewBox="0 0 14 14" aria-hidden="true"><circle cx="7" cy="7" r="6"/><path d="M4 4.5c1.5 0 2 1 1.5 2s1 1.5 0 3M9 3c-.5 1.5 1 2 2 2.5" stroke="#fff" stroke-width="1.2" fill="none"/></svg>
        www.tolvikcleaning.com
      </li>
    </ul>
  </section>

  <section class="card card--back">
    <div class="wordmark wordmark--back">Tolvik Commercial Cleaning</div>
  </section>
</body>
</html>
```